Profesional personal website needs design and business card

I need a business card with my professional name as a logo "Dorian Vitality" for my business. I am a Wellness Coach, consultant and trainer. So it should be professional, wellness oriented and modern.

Target Market(s)

Private clients, governments, corporations. Luxury and high market.

Industry/Entity Type

Health And Wellness

Contact Information for Business Card

Dorian Vitality should be the logo

Colors

Designer to choose colors to be used in the design.

Requirements
Must have
• Dorian Vitality
• Name: Tomás Lirandel
• Wellness Coach, Consultant & Trainer.
• Website: www.dorianvitality-example.com
• Phone:
• Spain (+34) 612 480 317
• (USA) +1 (555) 610 4829
Nice to have
• The most important is the design of "Dorian Vitality", as this is going to be my personal brand logo. It should be professional, wellness, high end and actual.
Should not have
• no golds, no baroque style..

```html
<!DOCTYPE html>
<html lang="en">
<head>
<meta charset="utf-8">
<title>Dorian Vitality – Business Card</title>
<link href="https://fonts.googleapis.com/css2?family=Lato:wght@400;700;900&display=swap" rel="stylesheet">
<style>
  :root {
    --page-bg: #e9e6e2;
    --card-face: #f3f1ee;
    --brand-blue: #1f6f9e;
    --brand-blue-deep: #155a84;
    --band-grey: #5e5a57;
    --text-light: #dfe6ea;
    --text-soft: #cfdbe3;
    --brand-ink: #1d5f8c;
  }
  html, body {
    margin: 0;
    width: 1200px;
    height: 1047px;
    overflow: hidden;
    background: var(--page-bg);
    font-family: "Lato", Arial, sans-serif;
  }
  .business-card {
    position: absolute;
    left: 100px;
    top: 252px;
    width: 1000px;
    height: 543px;
    border-radius: 26px;
    overflow: hidden;
    background: var(--card-face);
    box-shadow: 0 14px 40px rgba(0,0,0,0.18);
  }
  .card-shapes {
    position: absolute;
    inset: 0;
  }
  .holder-name {
    position: absolute;
    left: 40px;
    top: 105px;
    margin: 0;
    font-size: 40px;
    font-weight: 900;
    letter-spacing: 0.5px;
    color: var(--text-light);
  }
  .holder-title {
    position: absolute;
    left: 40px;
    top: 163px;
    margin: 0;
    font-size: 21px;
    font-weight: 400;
    color: var(--text-soft);
  }
  .contact-list {
    position: absolute;
    left: 34px;
    top: 326px;
    margin: 0;
    padding: 0;
    list-style: none;
  }
  .contact-item {
    display: flex;
    align-items: center;
    height: 32px;
    font-size: 21px;
    color: var(--text-soft);
  }
  .contact-icon {
    width: 22px;
    height: 22px;
    margin-right: 16px;
    flex: none;
  }
  .brand-name {
    position: absolute;
    left: 560px;
    width: 440px;
    top: 306px;
    margin: 0;
    text-align: center;
    font-size: 40px;
    font-weight: 900;
    letter-spacing: 1px;
    color: var(--brand-ink);
  }
</style>
</head>
<body>
  <section class="business-card" aria-label="Business card for Dorian Vitality">
    <svg class="card-shapes" width="1000" height="543" viewBox="0 0 1000 543" aria-hidden="true">
      <defs>
        <linearGradient id="blueSide" x1="0" y1="0" x2="1" y2="1">
          <stop offset="0" stop-color="#2a7fb3"/>
          <stop offset="1" stop-color="#16608e"/>
        </linearGradient>
      </defs>
      <path class="side-band" d="M572,0 C484,130 484,420 568,543 H0 V0 Z" fill="#5e5a57"/>
      <path class="side-blue" d="M556,0 C464,130 464,420 552,543 H0 V0 Z" fill="url(#blueSide)"/>
    </svg>

    <h1 class="holder-name">TOMÁS LIRANDEL</h1>
    <p class="holder-title">Wellness Coach, Consultant &amp; Trainer</p>

    <ul class="contact-list">
      <li class="contact-item">
        <svg class="contact-icon" viewBox="0 0 24 24"><path d="M6.6 10.8a15 15 0 0 0 6.6 6.6l2.2-2.2a1 1 0 0 1 1-.25 11.4 11.4 0 0 0 3.6.57 1 1 0 0 1 1 1V20a1 1 0 0 1-1 1A17 17 0 0 1 3 4a1 1 0 0 1 1-1h3.5a1 1 0 0 1 1 1c0 1.25.2 2.45.57 3.57a1 1 0 0 1-.25 1z" fill="#cfdbe3"/></svg>
        (+34) 612 480 317 (Spain)
      </li>
      <li class="contact-item">
        <svg class="contact-icon" viewBox="0 0 24 24"><path d="M6.6 10.8a15 15 0 0 0 6.6 6.6l2.2-2.2a1 1 0 0 1 1-.25 11.4 11.4 0 0 0 3.6.57 1 1 0 0 1 1 1V20a1 1 0 0 1-1 1A17 17 0 0 1 3 4a1 1 0 0 1 1-1h3.5a1 1 0 0 1 1 1c0 1.25.2 2.45.57 3.57a1 1 0 0 1-.25 1z" fill="#cfdbe3"/></svg>
        +1 (555) 610 4829 (USA)
      </li>
      <li class="contact-item">
        <svg class="contact-icon" viewBox="0 0 24 24"><rect x="2" y="5" width="20" height="14" rx="1.5" fill="#cfdbe3"/><path d="M3 6l9 7 9-7" fill="none" stroke="#1d6a99" stroke-width="1.6"/></svg>
        info@dorianvitality-example.com
      </li>
      <li class="contact-item">
        <svg class="contact-icon" viewBox="0 0 24 24" fill="none" stroke="#cfdbe3" stroke-width="1.6"><circle cx="12" cy="12" r="9"/><ellipse cx="12" cy="12" rx="4" ry="9"/><path d="M3 12h18M5 7h14M5 17h14"/></svg>
        www.dorianvitality-example.com
      </li>
    </ul>

    <p class="brand-name">DORIAN VITALITY</p>
  </section>
</body>
</html>
```